Business Cards Needed for Innovative Healthcare Marketing Company

We are a marketing company focused on healthcare. Our company is all about rebranding yourself renewing your image and generating results. The phoenix stands for "reborn" or "rising" which we provide new brands for our clients we take their old brands and renew it with creativity and innovation. I am looking for a business card with color dimension. I have attached an example of a card I think has the look and feel of what I am trying to accomplish. I like that the card example has black and grey font colors, I like the font placement and the small logo, I really like the use of the colors on the right those are the colors of my logo. My logo is phoenix so maybe incorporating flames similar to that design. I would like the back a solid color maybe red with an opaque version of the logo and website. As a marketing company I am always open to creative liberty!

Target Market(s)

Doctors and business professionals.

Industry/Entity Type

Marketing

Contact Information for Business Card

Valcorne Health Care Marketing
Marla Tenwick- CEO
#(512)638-2974
email-marla@valcorne.com
website- valcorne.com

Font styles to use
Sans Serif

Colors
ec1f27
f37122
ffc214
fbed22
fbf289
f04a50

Requirements
Must have
• The logo and required information
Nice to have
• icons by the information
Should not have
• child like font

```html
<!DOCTYPE html>
<html lang="en">
<head>
<meta charset="utf-8">
<title>Valcorne Health Care Marketing – Business Card</title>
<link rel="stylesheet" href="https://fonts.googleapis.com/css2?family=Open+Sans:wght@300;400;700&display=swap">
<style>
  :root {
    --backdrop: #3b3b3b;
    --card: #ffffff;
    --frame-red: #b8232a;
    --brand-red: #c62a2f;
    --brand-orange: #f37122;
    --text-grey: #555555;
  }
  * { box-sizing: border-box; margin: 0; padding: 0; }
  html, body {
    width: 1200px; height: 950px; overflow: hidden;
    background: var(--backdrop);
    font-family: "Open Sans", Arial, sans-serif;
  }
  .canvas { position: relative; width: 1200px; height: 950px; }
  .card {
    position: absolute; left: 250px;
    width: 700px; height: 400px;
    background: var(--card);
    border-radius: 22px;
  }
  .card::after {
    content: ""; position: absolute; inset: 18px;
    border: 2px solid var(--frame-red);
    border-radius: 14px; pointer-events: none;
  }
  .card--back { top: 50px; }
  .card--front { top: 500px; }

  /* back: centred brand name */
  .brand-lockup {
    position: absolute; left: 50%; top: 50%;
    transform: translate(-50%, -50%);
    display: flex; align-items: center; gap: 18px;
  }
  .brand-dot {
    width: 64px; height: 64px; border-radius: 50%;
    background: var(--brand-orange);
  }
  .brand-name {
    color: var(--brand-red); font-weight: 300; line-height: 1.1;
  }
  .brand-name__main { display: block; font-size: 40px; letter-spacing: 1px; }
  .brand-name__sub { display: block; font-size: 12px; letter-spacing: 1.6px; margin-top: 4px; }

  /* front: contact block + large brand mark area */
  .contact {
    position: absolute; left: 70px; top: 70px;
    list-style: none;
  }
  .contact__row {
    display: flex; align-items: center; gap: 14px;
    margin-bottom: 18px;
  }
  .icon {
    width: 26px; height: 26px; border-radius: 3px;
    background: var(--brand-red);
    display: flex; align-items: center; justify-content: center;
    flex: none;
  }
  .icon svg { width: 16px; height: 16px; }
  .person__name {
    color: var(--brand-red); font-weight: 700; font-size: 28px; line-height: 1.1;
  }
  .person__title {
    color: var(--brand-orange); font-weight: 700; font-size: 16px;
    margin: 2px 0 22px 40px;
  }
  .contact__text { color: var(--text-grey); font-size: 19px; }

  .front-mark {
    position: absolute; right: 70px; top: 70px;
    width: 220px; height: 260px;
    display: flex; flex-direction: column; align-items: center; justify-content: center; gap: 18px;
  }
  .front-mark .brand-dot { width: 150px; height: 150px; }
  .front-mark .brand-name { font-size: 30px; letter-spacing: 1px; }
</style>
</head>
<body>
<main class="canvas">

  <section class="card card--back" aria-label="Card back">
    <div class="brand-lockup">
      <span class="brand-dot"></span>
      <p class="brand-name">
        <span class="brand-name__main">VALCORNE</span>
        <span class="brand-name__sub">HEALTH CARE MARKETING</span>
      </p>
    </div>
  </section>

  <section class="card card--front" aria-label="Card front">
    <ul class="contact">
      <li class="contact__row">
        <span class="icon">
          <svg viewBox="0 0 16 16"><circle cx="8" cy="5" r="3.2" fill="#fff"/><path d="M2 15c0-4 2.7-6 6-6s6 2 6 6z" fill="#fff"/></svg>
        </span>
        <span class="person__name">Marla Tenwick</span>
      </li>
    </ul>
    <ul class="contact" style="top:112px">
      <li><p class="person__title">CEO</p></li>
      <li class="contact__row">
        <span class="icon">
          <svg viewBox="0 0 16 16"><path d="M4 1.5l2.4 3-1.5 1.6c.8 1.9 2.1 3.2 4 4l1.6-1.5 3 2.4-1.5 2.5C6.6 13.4 2.6 9.4 1.5 3z" fill="#fff"/></svg>
        </span>
        <span class="contact__text">(512)638-2974</span>
      </li>
      <li class="contact__row">
        <span class="icon">
          <svg viewBox="0 0 16 16"><rect x="1.5" y="3.5" width="13" height="9" rx="1" fill="#fff"/><path d="M2 4.2l6 4.6 6-4.6" fill="none" stroke="#c62a2f" stroke-width="1.3"/></svg>
        </span>
        <span class="contact__text">marla@valcorne.com</span>
      </li>
      <li class="contact__row">
        <span class="icon">
          <svg viewBox="0 0 16 16" fill="none" stroke="#fff" stroke-width="1.4"><circle cx="8" cy="8" r="6"/><ellipse cx="8" cy="8" rx="2.6" ry="6"/><path d="M2 8h12"/></svg>
        </span>
        <span class="contact__text">www.valcorne.com</span>
      </li>
    </ul>

    <div class="front-mark">
      <span class="brand-dot"></span>
      <span class="brand-name">VALCORNE</span>
    </div>
  </section>

</main>
</body>
</html>
```